The Marrowby Hotel Flyer

it is for a Pub that has been in the area for a long time but now we have changed the name and taken over as new owners and now have to try to get all the locals back, eating and drinking..

This Flyer is to try get all the locals to come try the new Marrowby Hotel.

We have a great new menu with daily food deals
Craft beers
Week nights Live music
Tuesday Comedy night
Sunday live music

Industry/Entity Type

Hotel

```html
<!DOCTYPE html>
<html lang="en">
<head>
<meta charset="utf-8">
<title>The Marrowby Hotel Flyer</title>
<link rel="stylesheet" href="https://fonts.googleapis.com/css2?family=Arimo:wght@400;700&display=swap">
<style>
  :root {
    --navy: #14287a;
    --ink: #1f2a4f;
    --paper: #ffffff;
    --glass-edge: #dfe1e3;
    --glass-mid: #f6f7f7;
    --white: #ffffff;
  }
  html, body { margin: 0; padding: 0; overflow: hidden; background: var(--paper); }
  .flyer {
    position: relative;
    width: 848px;
    height: 1200px;
    overflow: hidden;
    background: var(--paper);
    font-family: "Arimo", Arial, sans-serif;
    color: var(--navy);
  }
  .backdrop, .graphics { position: absolute; inset: 0; }
  .line {
    position: absolute;
    left: 0;
    width: 848px;
    margin: 0;
    text-align: center;
    line-height: 1;
  }
  .wide { transform: scaleX(1.25); transform-origin: center; }
  .venue-name { font-weight: 700; }
  .venue-name--the { top: 40px; font-size: 42px; }
  .venue-name--main { top: 82px; font-size: 128px; }
  .venue-name--hotel { top: 232px; font-size: 42px; }
  .address { top: 311px; font-size: 24px; font-weight: 700; transform: scaleX(1.45); }
  .invite { font-size: 27px; font-weight: 400; }
  .invite--come { top: 413px; }
  .invite--and { top: 528px; }
  .headline { font-size: 48px; font-weight: 700; transform: scaleX(1.2); }
  .headline--menu { top: 455px; }
  .headline--beers { top: 570px; }
  .mug-label {
    position: absolute;
    top: 712px;
    width: 181px;
    margin: 0;
    text-align: center;
    color: var(--white);
    font-size: 42px;
    font-weight: 700;
    line-height: 44px;
    transform: scaleX(1.3);
  }
  .mug-label--uni { left: 207px; }
  .mug-label--daily { left: 472px; }
  .event { position: absolute; margin: 0; text-align: center; }
  .event p { margin: 0; }
  .event__when { font-size: 27px; font-weight: 400; line-height: 27px; transform: scaleX(1.35); }
  .event__what { font-size: 46px; font-weight: 700; line-height: 43px; transform: scaleX(1.1); }
  .event--music { left: 133px; width: 280px; top: 930px; }
  .event--music .event__what { margin-top: 22px; }
  .event--comedy { left: 460px; width: 260px; top: 963px; }
  .event--comedy .event__what { margin-top: 44px; }
</style>
</head>
<body>
<main class="flyer">
  <svg class="backdrop" width="848" height="1200" viewBox="0 0 848 1200" role="img" aria-label="Photo of an empty pint glass filling the background">
    <defs>
      <linearGradient id="glassTone" x1="0" y1="0" x2="1" y2="0">
        <stop offset="0" stop-color="var(--glass-edge)"/>
        <stop offset="0.15" stop-color="var(--glass-mid)"/>
        <stop offset="0.85" stop-color="var(--glass-mid)"/>
        <stop offset="1" stop-color="var(--glass-edge)"/>
      </linearGradient>
    </defs>
    <rect width="848" height="1200" fill="url(#glassTone)"/>
  </svg>

  <svg class="graphics" width="848" height="1200" viewBox="0 0 848 1200">
    <g class="divider" stroke="var(--navy)" stroke-width="3" aria-hidden="true">
      <line x1="303" y1="369" x2="552" y2="369"/>
      <line x1="303" y1="380" x2="552" y2="380"/>
      <line x1="303" y1="887" x2="552" y2="887"/>
      <line x1="303" y1="901" x2="552" y2="901"/>
    </g>
    <rect class="mug-area" x="160" y="648" width="228" height="220" rx="10" fill="var(--ink)" role="img" aria-label="Illustration of a frothy beer mug"/>
    <rect class="mug-area" x="472" y="648" width="226" height="220" rx="10" fill="var(--ink)" role="img" aria-label="Illustration of a frothy beer mug"/>
    <rect class="pint-area" x="388" y="958" width="84" height="160" fill="var(--ink)" role="img" aria-label="Illustration of a pint glass"/>
  </svg>

  <h1 class="line venue-name venue-name--the">The</h1>
  <p class="line venue-name venue-name--main">Marrowby</p>
  <p class="line venue-name venue-name--hotel">Hotel</p>
  <p class="line address">41/45 Tallowin St Cnr of Hazel st</p>

  <p class="line invite invite--come wide">Come try our</p>
  <p class="line headline headline--menu">Great New Menu</p>
  <p class="line invite invite--and wide">and</p>
  <p class="line headline headline--beers">Craft Beers</p>

  <p class="mug-label mug-label--uni">Uni<br>Food<br>Deals</p>
  <p class="mug-label mug-label--daily">Daily<br>Food<br>Deals</p>

  <div class="event event--music">
    <p class="event__when">Week Nights<br>+<br>Sunday</p>
    <p class="event__what">Live<br>Music</p>
  </div>
  <div class="event event--comedy">
    <p class="event__when">Tuesday</p>
    <p class="event__what">Comedy<br>Night</p>
  </div>
</main>
</body>
</html>
```